Travel Agency Website - Simple General

Need a 7 page simple design that is pretty repetitive. Need to be able to load quickly that is SEO optimized. Trying to give ideas on what they can do, be personal as we are local, but at the same time come across as professional and get information easily with little burden.

- Landing Page
- Brimwell Vacations Page
- Family Trips
- Road Trips from Texas
- Other Destinations
- About Us Page
- Contact Us Page

Target Market(s)

Families

Coding

Coded - Design and coding required

Number of Pages Required

5+ page

Colors

Designer to choose colors to be used in the design.

Requirements
Must have
• Like it to flow easily with our logo. Use that for colors, etc.

```html
<!DOCTYPE html>
<html lang="en">
<head>
<meta charset="utf-8">
<title>Meadowlark Journeys – Travel Planning Made Magical</title>
<link href="https://fonts.googleapis.com/css2?family=Lobster&family=Montserrat:wght@500;600;700&family=Roboto:wght@400;500&display=swap" rel="stylesheet">
<style>
:root{
  --teal-dark:#1e5b62;
  --teal:#2b7f83;
  --teal-mid:#236e74;
  --gold:#c39a4b;
  --ink:#2c2c2c;
  --muted:#555;
  --white:#fff;
}
*{box-sizing:border-box;margin:0;padding:0}
html,body{width:1200px;height:3011px;overflow:hidden;background:var(--white);font-family:'Roboto',sans-serif;color:var(--ink)}
.page{position:relative;width:1200px;height:3011px;overflow:hidden}
.abs{position:absolute}
.btn{position:absolute;display:flex;align-items:center;justify-content:center;border-radius:30px;font-family:'Montserrat',sans-serif;font-weight:700;font-size:14px;text-transform:uppercase;color:var(--white);background:var(--teal-dark)}
.btn--gold{background:var(--gold)}
.btn--outline{background:var(--white);color:var(--teal-dark);border:3px solid var(--teal-dark)}
.script{font-family:'Lobster',cursive;font-weight:400}
/* header */
.topbar{left:0;top:0;width:1200px;height:79px;background:var(--white)}
.brand{left:140px;top:10px;width:176px;height:150px;border-radius:50%;background:#f3f6f4;border:3px solid #cfe0de;display:flex;flex-direction:column;align-items:center;justify-content:center;z-index:5}
.brand span{font-family:'Montserrat',sans-serif;font-weight:700;font-size:17px;color:var(--teal-dark);text-align:center;line-height:1.2}
.phone{left:664px;top:22px;display:flex;align-items:center;gap:12px;font-family:'Montserrat',sans-serif;font-weight:500;font-size:18px;color:var(--ink)}
.icon-dot{width:34px;height:34px;border-radius:50%;background:var(--gold);display:flex;align-items:center;justify-content:center}
.nav{left:0;top:79px;width:1200px;height:50px;background:var(--teal)}
.nav ul{list-style:none;display:flex;position:absolute;left:310px;top:0;height:50px}
.nav li{height:50px;display:flex;align-items:center;padding:0 11px;font-family:'Montserrat',sans-serif;font-weight:600;font-size:14px;color:var(--white)}
.nav li.active{background:var(--teal-dark);padding:0 17px}
/* hero */
.hero{left:0;top:129px;width:1200px;height:700px;background:linear-gradient(180deg,#e9d8bf 0%,#e8b880 35%,#c9a57d 60%,#d7b896 80%,#e9cfa9 100%)}
.hero h1{left:145px;top:138px;font-size:72px;line-height:70px;color:var(--teal-dark)}
.hero h1 em{font-style:normal;color:var(--gold)}
.hero p{left:145px;top:302px;font-size:21px;line-height:32px;color:#2a2a2a;font-family:'Montserrat',sans-serif;font-weight:500}
.dots span{position:absolute;left:1131px;width:11px;height:11px;border-radius:50%;background:var(--white)}
/* destinations */
.sec-title{left:0;top:930px;width:1200px;text-align:center;font-size:60px;color:var(--teal-dark)}
.sec-title em{font-style:normal;color:var(--gold)}
.card{position:absolute;top:1070px;width:292px;height:520px}
.card__img{position:absolute;left:0;top:0;width:292px;height:375px;border-radius:22px}
.card__box{position:absolute;left:3px;top:305px;width:262px;height:215px;background:var(--white);border-radius:18px;box-shadow:0 10px 30px rgba(0,0,0,.1);text-align:center}
.card__box h3{margin-top:36px;font-size:21px;font-weight:500;color:#333}
.card__box p{margin-top:10px;font-size:16px;line-height:24px;color:var(--muted)}
.heart{position:absolute;top:22px;right:22px;width:26px;height:26px;border-radius:50%;background:var(--white);display:flex;align-items:center;justify-content:center}
/* about */
.about-bg{left:0;top:1700px;width:1200px;height:760px;background:linear-gradient(180deg,#a9c6c9 0%,#d3e2e2 30%,#f2f6f5 60%,#fff 100%)}
.about h2{left:145px;top:1895px;font-size:60px;color:var(--teal-dark)}
.about p{left:146px;top:1980px;width:413px;font-size:16px;line-height:30px;color:var(--muted);text-align:justify}
.photo{position:absolute;border:5px solid var(--white);border-radius:12px;box-shadow:0 12px 30px rgba(0,0,0,.2)}
/* cta & footer */
.cta-bg{left:0;top:2440px;width:1200px;height:571px;background:var(--teal-dark)}
.cta h2{left:143px;top:2525px;font-size:56px;line-height:68px;color:var(--white)}
.divider{left:0;top:2708px;width:1200px;height:1px;background:rgba(255,255,255,.18)}
.contact-row{left:0;top:2760px;width:1200px;display:flex;justify-content:center;gap:40px;font-family:'Montserrat',sans-serif;font-weight:500;font-size:20px;color:var(--white)}
.contact-row div{display:flex;align-items:center;gap:10px}
.foot-nav{left:0;top:2828px;width:1200px;display:flex;justify-content:center;gap:23px;list-style:none;font-family:'Montserrat',sans-serif;font-weight:600;font-size:14px;color:var(--white)}
.copy{left:0;top:2873px;width:1200px;text-align:center;font-family:'Montserrat',sans-serif;font-size:15px;color:rgba(255,255,255,.9)}
.social{left:552px;top:2922px;display:flex;gap:10px}
.social span{width:42px;height:42px;border-radius:50%;border:2px solid var(--white)}
</style>
</head>
<body>
<div class="page">

  <!-- header -->
  <header class="abs topbar"></header>
  <div class="abs brand"><span>Meadowlark<br>Journeys</span></div>
  <div class="abs phone"><span class="icon-dot"><svg width="16" height="16" viewBox="0 0 24 24"><path fill="#fff" d="M6.6 10.8a15 15 0 006.6 6.6l2.2-2.2c.3-.3.7-.4 1-.2 1.1.4 2.3.6 3.6.6.6 0 1 .4 1 1V20c0 .6-.4 1-1 1A17 17 0 013 4c0-.6.4-1 1-1h3.5c.6 0 1 .4 1 1 0 1.3.2 2.5.6 3.6.1.3 0 .7-.2 1z"/></svg></span>Phone : +1 111 111 1111</div>
  <div class="btn" style="left:907px;top:15px;width:148px;height:46px;font-weight:600">Contact Us</div>
  <nav class="abs nav"><ul>
    <li class="active">Home</li><li>Brimwell Vacations</li><li>Family Trips</li><li>Road Trips from Texas</li><li>Destinations</li><li>About Us</li>
  </ul></nav>

  <!-- hero -->
  <section class="abs hero" role="img" aria-label="Family running hand in hand along the beach at sunset">
    <h1 class="abs script">Travel Planning<br><em>Made Magical</em></h1>
    <p class="abs">Stress-free vacations designed for families,<br>dreamers, and explorers.</p>
    <div class="btn" style="left:145px;top:399px;width:202px;height:58px">Start Planning</div>
    <div class="btn btn--outline" style="left:357px;top:399px;width:258px;height:58px">Explore Destinations</div>
    <div class="dots"><span style="top:541px"></span><span style="top:565px;background:var(--teal)"></span><span style="top:589px"></span></div>
  </section>
  <svg class="abs" style="left:0;top:740px" width="1200" height="100" viewBox="0 0 1200 100">
    <path d="M0 100V50C120 0 250 20 370 65 460 95 540 45 600 12 660 45 740 95 830 65 950 20 1080 0 1200 50V100Z" fill="#fff"/>
    <path d="M0 50C120 0 250 20 370 65 460 95 540 45 600 12 660 45 740 95 830 65 950 20 1080 0 1200 50" fill="none" stroke="var(--teal)" stroke-width="6"/>
  </svg>

  <!-- destinations -->
  <h2 class="abs script sec-title">Wherever You <em>Want to Go</em></h2>
  <div class="card" style="left:0">
    <div class="card__img" role="img" aria-label="Canal-side medieval town with a church tower" style="background:linear-gradient(180deg,#6f88b4,#9a7b63 60%,#6b5a52)"></div>
    <span class="heart"><svg width="12" height="12" viewBox="0 0 24 24"><path d="M12 21l-9-9a5 5 0 017-7l2 2 2-2a5 5 0 017 7z" fill="none" stroke="var(--teal)" stroke-width="2.5"/></svg></span>
    <div class="card__box"><h3>Brimwell Vacations</h3><p>Sed ut perspiciatis unde<br>omnis iste natus sit</p><div class="btn" style="left:56px;top:135px;width:152px;height:50px">Read More</div></div>
  </div>
  <div class="card" style="left:302px">
    <div class="card__img" role="img" aria-label="Family in sun hats overlooking a city skyline" style="background:linear-gradient(180deg,#dfe3ea,#cdbfae 70%,#a89a86);border:2px solid var(--gold);outline:6px solid #fff;outline-offset:-9px"></div>
    <span class="heart"><svg width="12" height="12" viewBox="0 0 24 24"><path d="M12 21l-9-9a5 5 0 017-7l2 2 2-2a5 5 0 017 7z" fill="none" stroke="var(--teal)" stroke-width="2.5"/></svg></span>
    <div class="card__box" style="left:11px"><h3>Family Trips</h3><p>Sed ut perspiciatis unde<br>omnis iste natus sit</p><div class="btn btn--gold" style="left:56px;top:135px;width:152px;height:50px">Read More</div></div>
  </div>
  <div class="card" style="left:611px">
    <div class="card__img" role="img" aria-label="View from a car dashboard onto an open highway" style="background:linear-gradient(180deg,#f0e6da,#cfc4b6 40%,#2a2a2a 60%,#111)"></div>
    <span class="heart"><svg width="12" height="12" viewBox="0 0 24 24"><path d="M12 21l-9-9a5 5 0 017-7l2 2 2-2a5 5 0 017 7z" fill="none" stroke="var(--teal)" stroke-width="2.5"/></svg></span>
    <div class="card__box" style="left:14px"><h3>Road Trips from Texas</h3><p>Sed ut perspiciatis unde<br>omnis iste natus sit</p><div class="btn" style="left:56px;top:135px;width:152px;height:50px">Read More</div></div>
  </div>
  <div class="card" style="left:922px">
    <div class="card__img" role="img" aria-label="Winding road bridge through green forest" style="background:linear-gradient(160deg,#5f8b3f,#3f7a2e 50%,#8aa06c)"></div>
    <span class="heart"><svg width="12" height="12" viewBox="0 0 24 24"><path d="M12 21l-9-9a5 5 0 017-7l2 2 2-2a5 5 0 017 7z" fill="none" stroke="var(--teal)" stroke-width="2.5"/></svg></span>
    <div class="card__box" style="left:14px"><h3>Other Destinations</h3><p>Sed ut perspiciatis unde<br>omnis iste natus sit</p><div class="btn" style="left:56px;top:135px;width:152px;height:50px">Read More</div></div>
  </div>

  <!-- about -->
  <div class="abs about-bg"></div>
  <svg class="abs" style="left:0;top:1700px" width="1200" height="100" viewBox="0 0 1200 100">
    <path d="M0 0H1200V50C1080 0 950 20 830 65 740 95 660 45 600 12 540 45 460 95 370 65 250 20 120 0 0 50Z" fill="#fff"/>
    <path d="M0 50C120 0 250 20 370 65 460 95 540 45 600 12 660 45 740 95 830 65 950 20 1080 0 1200 50" fill="none" stroke="var(--teal)" stroke-width="6"/>
  </svg>
  <div class="about">
    <h2 class="abs script">About Us</h2>
    <p class="abs">Sed ut perspiciatis unde omnis iste natus error sit voluptatem accusantium doloremque laudantium, totam rem aperiam, eaque ipsa quae ab illo inventore veritatis et quasi architecto beatae vitae dicta sunt explicabo. Nemo enim ipsam voluptatem quia voluptas sit aspernatur aut odit aut fugit, sed quia consequuntur magni dolores eos qui ratione voluptatem sequi nesciunt.</p>
    <div class="btn" style="left:147px;top:2216px;width:152px;height:50px">Read More</div>
  </div>
  <div class="photo" role="img" aria-label="Friends cheering on a car roof by the sea" style="left:624px;top:1834px;width:422px;height:244px;background:linear-gradient(180deg,#55b7dc,#2aa1c6 60%,#2a6aa0)"></div>
  <div class="photo" role="img" aria-label="Desert city skyline at dusk" style="left:706px;top:2030px;width:420px;height:220px;transform:rotate(-19deg);background:linear-gradient(180deg,#a5bccd,#d3c2a6 50%,#7a6a55)"></div>
  <div class="photo" role="img" aria-label="Hikers below snowy mountains" style="left:597px;top:2240px;width:300px;height:180px;transform:rotate(-19deg);background:linear-gradient(180deg,#3d8fc7,#b8c8d2 45%,#8d6d45)"></div>

  <!-- cta -->
  <div class="abs cta-bg"></div>
  <svg class="abs" style="left:0;top:2385px" width="1200" height="110" viewBox="0 0 1200 110">
    <path d="M0 0H1200V60C1080 15 950 30 830 75 740 105 660 60 600 20 540 60 460 105 370 75 250 30 120 15 0 60Z" fill="#fff"/>
    <path d="M0 60C120 15 250 30 370 75 460 105 540 60 600 20 660 60 740 105 830 75 950 30 1080 15 1200 60" fill="none" stroke="var(--teal)" stroke-width="6"/>
    <path d="M0 78C120 33 250 48 370 93 460 123 540 78 600 38 660 78 740 123 830 93 950 48 1080 33 1200 78" fill="none" stroke="#fff" stroke-width="4"/>
  </svg>
  <div class="cta"><h2 class="abs script">Ready to Start Your<br>Next Adventure?</h2></div>
  <div class="btn btn--gold" style="left:865px;top:2575px;width:190px;height:50px">Plan Your Trip</div>
  <div class="abs divider"></div>

  <footer>
    <div class="abs contact-row">
      <div><svg width="30" height="30" viewBox="0 0 30 30"><circle cx="15" cy="15" r="14" fill="none" stroke="#fff" stroke-width="2"/><path fill="#fff" d="M11 10l2 3-1.4 1.4a8 8 0 004 4L17 17l3 2-1.5 2A10 10 0 019 11z"/></svg>+1 111.111.1111</div>
      <div><span class="icon-dot" style="width:30px;height:30px"><svg width="14" height="10" viewBox="0 0 14 10"><rect width="14" height="10" rx="1" fill="#fff"/><path d="M0 0l7 5 7-5" fill="none" stroke="var(--gold)"/></svg></span>hello@meadowlarkjourneys.com</div>
    </div>
    <ul class="abs foot-nav"><li>Home</li><li>Brimwell Vacations</li><li>Family Trips</li><li>Road Trips from Texas</li><li>Destinations</li><li>About Us</li><li>Contact Us</li></ul>
    <p class="abs copy">© 2026 Companyname. All rights reserved &nbsp; | &nbsp; Privacy &nbsp; | &nbsp; Terms of Use</p>
    <div class="abs social" aria-label="Social media links"><span></span><span></span></div>
  </footer>
</div>
</body>
</html>
```